Corvane Holdings , new business card design

investment firm with corporate clients . need double sided business card , vertical and horizontal options ,logo must be clear. prefer pantone colors only and sharp design. website also www.corvane.ae

Khalid Bin Tarrafi
Managing Director
Tel. +971 4 387 2940
Mobile +971 50 518 2403
khalid@corvane.ae
Q-Span Plaza, officw 18-B07, Warqa Gardens, Dubai

Contact Information for Business Card

Khalid Bin Tarrafi
Managing Director

Font styles to use
Serif

Colors

Designer to choose colors to be used in the design.

```html
<!DOCTYPE html>
<html lang="en">
<head>
<meta charset="utf-8">
<title>Corvane Holdings — Business Card</title>
<link rel="stylesheet" href="https://fonts.googleapis.com/css2?family=Didact+Gothic&display=swap">
<style>
  :root {
    --page-bg: #a0a0a0;
    --card-front: #cbcbcb;
    --card-back: #1f2a5e;
    --ink-dark: #141414;
    --brand-blue: #4a7aa6;
    --ink-light: #dcd8ee;
    --shadow: rgba(0, 0, 0, 0.28);
  }
  * { margin: 0; padding: 0; box-sizing: border-box; }
  html, body {
    width: 1200px;
    height: 1000px;
    overflow: hidden;
  }
  body {
    background: var(--page-bg);
    font-family: "Didact Gothic", "Century Gothic", sans-serif;
    display: flex;
    align-items: center;
    justify-content: center;
    gap: 44px;
  }
  .card {
    width: 520px;
    height: 300px;
    position: relative;
    box-shadow: 0 6px 18px var(--shadow);
  }

  /* Front */
  .card--front {
    background: var(--card-front);
    display: flex;
    flex-direction: column;
    align-items: center;
    justify-content: center;
  }
  .brand {
    display: flex;
    align-items: center;
    gap: 16px;
  }
  .brand__square {
    width: 26px;
    height: 26px;
    background: var(--brand-blue);
  }
  .brand__name {
    font-size: 34px;
    letter-spacing: 0.32em;
    color: var(--ink-dark);
    line-height: 1;
    text-transform: uppercase;
  }
  .website {
    margin-top: 46px;
    font-size: 17px;
    letter-spacing: 0.42em;
    color: var(--ink-dark);
    text-transform: uppercase;
  }

  /* Back */
  .card--back {
    background: var(--card-back);
    color: var(--ink-light);
  }
  .holder {
    position: absolute;
    top: 30px;
    left: 30px;
  }
  .holder__name {
    font-size: 20px;
    line-height: 1.1;
  }
  .holder__title {
    font-size: 12px;
    margin-top: 2px;
  }
  .contact {
    position: absolute;
    left: 268px;
    top: 150px;
    font-size: 13.5px;
    line-height: 1.32;
  }
  .contact__address {
    margin-top: 18px;
  }
</style>
</head>
<body>
  <section class="card card--front" aria-label="Business card front">
    <div class="brand">
      <span class="brand__square" aria-hidden="true"></span>
      <span class="brand__name">Corvane Holdings</span>
    </div>
    <p class="website">corvane.ae</p>
  </section>

  <section class="card card--back" aria-label="Business card back">
    <div class="holder">
      <p class="holder__name">Khalid Bin Tarrafi</p>
      <p class="holder__title">Director</p>
    </div>
    <div class="contact">
      <p>Tel. +971 4 387 2940</p>
      <p>Mobile +971 50 518 2403</p>
      <p>khalid@corvane.ae</p>
      <div class="contact__address">
        <p>Q-Span Plaza, officw 18-B07</p>
        <p>Warqa Gardens, Dubai</p>
      </div>
    </div>
  </section>
</body>
</html>
```